tallow-brook.com

We are a small dollar lending company that will revolutionize the industry. We will do this by being completely transparent, fee free, etc and an interest rate that normal people can afford to pay. Over 10X less than our competition. We only allow our members to pay bills " bills paid fast", within 72 hours. Payday loans typically charge from 390%-600% with a terrible payback structure. We charge 36%, period, with a payback structure over 12 months. Our site will be very simple and easy to use but elegant at the same time. We do not want the site to be too busy, less is more and easier. We will have; Home, The Story, Why tallowbrook.com, Are you eligible? Members, Clients. To become a member you have to be referred by a current client of tallowbrook.com. A lot of the busy stuff will be saved for the Members and Clients sections. The feel must be elegant, easy to use and very simple to understand. I am looking for the green, white and black combinations of colors, very similar to my logo that was designed by Fernquillo.

```html
<!DOCTYPE html>
<html lang="en">
<head>
<meta charset="utf-8">
<title>Tallow Brook – Bills Paid Fast</title>
<link href="https://fonts.googleapis.com/css2?family=Open+Sans:wght@300;400;600&family=Arimo:ital,wght@0,400;0,700;1,400&display=swap" rel="stylesheet">
<style>
:root{
  --green:#8cc63f;
  --green-dark:#7ab32e;
  --ink:#222;
  --body:#555;
  --strip:#3a3a3a;
  --footer:#444;
  --footer-base:#363636;
  --line:#dcdcdc;
  --white:#fff;
}
*{margin:0;padding:0;box-sizing:border-box}
html,body{width:1200px;height:2723px;overflow:hidden;background:var(--white)}
body{position:relative;font-family:"Arimo",Arial,sans-serif;color:var(--body)}
.abs{position:absolute}

/* header */
.site-header{left:0;top:0;width:1200px;height:65px;background:var(--green)}
.brand{left:172px;top:12px;display:flex;align-items:center;gap:8px;color:var(--white);font-family:"Open Sans",sans-serif;font-weight:600;font-size:19px;letter-spacing:.5px}
.brand-dot{width:34px;height:34px;border-radius:50%;border:3px solid var(--white)}
.main-nav a{position:absolute;top:24px;color:var(--white);font-size:13px;text-decoration:none;white-space:nowrap}

/* hero */
.hero{left:0;top:65px;width:1200px;height:498px;background:linear-gradient(120deg,#d9e4ea 0%,#eef3f5 35%,#c9d6dc 60%,#7fa9b8 85%,#4e8397 100%)}
.hero-title{left:169px;top:395px;font-family:"Open Sans",sans-serif;font-weight:300;font-size:40px;color:#111}
.hero-sub{left:172px;top:460px;font-size:19px;color:#111}
.hero-arrow{top:441px;width:40px;height:40px;background:rgba(255,255,255,.35);border:1px solid rgba(255,255,255,.5)}
.side-tab{left:0;width:44px;height:124px;background:var(--green);color:var(--white);font-size:11px;letter-spacing:1px}
.side-tab span{position:absolute;left:12px;top:14px;writing-mode:vertical-rl;transform:rotate(180deg)}
.side-tab svg{position:absolute;left:12px;bottom:14px}

/* bill strip */
.bill-strip{left:0;top:563px;width:1200px;height:112px;background:var(--strip)}
.bill{top:0;width:282px;height:112px;padding:24px 0 0 102px;color:#999;font-size:10.5px;line-height:18px}
.bill.active{background:var(--green);color:var(--white)}
.bill h4{font-weight:400;font-size:13.5px;color:var(--green);margin-bottom:6px}
.bill.active h4{color:var(--white)}
.bill svg{position:absolute;left:34px;top:30px}
.strip-arrow{top:48px}

/* welcome */
.welcome-title{left:0;width:1200px;top:735px;text-align:center;font-family:"Open Sans",sans-serif;font-weight:400;font-size:30px;color:#111}
.welcome-title b{font-weight:400;color:var(--green)}
.welcome-tag{left:0;width:1200px;top:798px;text-align:center;font-size:19px;color:#111}
.welcome-text{left:190px;width:820px;top:838px;text-align:center;font-size:11.5px;line-height:22px}
.divider{left:171px;top:940px;width:857px;height:2px;background:var(--line)}

.feature{top:966px;width:263px}
.feature h3{font-family:"Open Sans",sans-serif;font-weight:400;font-size:17px;color:var(--green);height:39px}
.feature .photo{width:263px;height:142px}
.feature p{font-size:11px;line-height:19px;margin-top:12px;height:90px}
.btn{display:inline-block;background:var(--green);color:var(--white);font-size:10.5px;width:89px;height:28px;line-height:28px;text-align:center}

/* dark band */
.promo{left:0;top:1329px;width:1200px;height:383px;background:linear-gradient(135deg,#2d3234 0%,#1c2022 50%,#2a2f31 100%)}
.promo h2{position:absolute;left:0;width:1200px;top:40px;text-align:center;font-family:"Open Sans",sans-serif;font-weight:300;font-size:26px;color:var(--green)}
.promo p{position:absolute;left:205px;width:790px;text-align:center;color:var(--white);font-size:11.5px;line-height:23px}
.promo .outline-btn{position:absolute;left:459px;top:274px;width:283px;height:49px;border:1px solid var(--green);color:var(--green);font-size:13.5px;text-align:center;line-height:47px}

/* clients */
.section-title{left:0;width:1200px;text-align:center;font-family:"Open Sans",sans-serif;font-weight:300;font-size:38px}
.clients-text{left:190px;width:820px;top:1822px;text-align:center;font-size:11.5px;line-height:22px}
.client{width:194px;height:104px;border:1px solid #e2e2e2;display:flex;align-items:center;justify-content:center;gap:8px;color:#aaa;font-size:17px;white-space:nowrap}
.client i{width:14px;height:14px;border-radius:50%;background:#c4c4c4;display:block;flex:none}

/* testimonials */
.testimonials{left:0;top:2173px;width:1200px;height:314px;background:var(--green)}
.quote{position:absolute;left:290px;width:615px;top:117px;text-align:center;color:var(--white);font-size:10.5px;line-height:23px}
.qmark{position:absolute;color:var(--white);font-family:Georgia,serif;font-style:italic;font-size:34px}
.t-arrow{position:absolute;top:137px;width:28px;height:28px;background:rgba(255,255,255,.25)}
.byline{position:absolute;left:0;width:1200px;text-align:center;color:var(--white);font-style:italic;font-size:10.5px}

/* footer */
.site-footer{left:31px;top:2487px;width:1169px;height:190px;background:var(--footer)}
.footer-col{top:2520px;font-size:11px;color:var(--white);line-height:23px}
.social{left:889px;display:flex;align-items:center;gap:10px;color:var(--white);font-size:11px}
.social i{width:28px;height:28px;border-radius:50%;background:#6a6a6a;display:block}
.footer-base{left:31px;top:2677px;width:1169px;height:46px;background:var(--footer-base);text-align:center;line-height:46px;font-size:10.5px;color:#999}
</style>
</head>
<body>

<header class="abs site-header">
  <div class="abs brand"><span class="brand-dot"></span>TALLOW BROOK</div>
  <nav class="main-nav">
    <a style="left:509px">Home</a>
    <a style="left:584px">The Story</a>
    <a style="left:680px">Why tallowbrook.com</a>
    <a style="left:833px">Are you eligible? Members</a>
    <a style="left:1004px">Clients</a>
  </nav>
</header>

<section class="abs hero" role="img" aria-label="Photo of hands typing on a white laptop keyboard"></section>
<h1 class="abs hero-title">Bills Paid Fast</h1>
<p class="abs hero-sub">We charge only 36% and give over 12 months time to pay back, no fees, hidden costs etc.</p>
<div class="abs hero-arrow" style="left:944px"><svg width="40" height="40"><path d="M23 13l-7 7 7 7" fill="none" stroke="#fff" stroke-width="1.5"/></svg></div>
<div class="abs hero-arrow" style="left:988px"><svg width="40" height="40"><path d="M17 13l7 7-7 7" fill="none" stroke="#fff" stroke-width="1.5"/></svg></div>

<div class="abs side-tab" style="top:181px"><span>REGISTER</span><svg width="18" height="20"><rect x="2" y="1" width="14" height="18" fill="none" stroke="#fff" stroke-width="1.5"/><path d="M5 7h8M5 11h8M5 15h5" stroke="#fff"/></svg></div>
<div class="abs side-tab" style="top:312px"><span>LOGIN</span><svg width="18" height="16"><rect x="1" y="3" width="16" height="12" rx="2" fill="#fff"/><circle cx="9" cy="9" r="2.5" fill="#8cc63f"/></svg></div>

<section class="abs bill-strip">
  <svg class="abs strip-arrow" style="left:146px" width="12" height="16"><path d="M9 2L3 8l6 6" fill="none" stroke="#999" stroke-width="1.5"/></svg>
  <div class="abs bill active" style="left:183px">
    <svg width="40" height="48"><path d="M14 2v12M26 2v12" stroke="#fff" stroke-width="3"/><path d="M8 14h24v8c0 8-5 12-12 12S8 30 8 22z" fill="#fff"/><path d="M20 34v8c0 3-3 5-8 5" fill="none" stroke="#fff" stroke-width="3"/></svg>
    <h4>Electricity Bill</h4>It is a long established fact that a<br>reader will be distracted...
  </div>
  <div class="abs bill" style="left:465px">
    <svg width="40" height="48"><rect x="6" y="4" width="20" height="38" rx="2" fill="none" stroke="#999" stroke-width="2"/><rect x="10" y="9" width="12" height="9" fill="#999"/><path d="M26 14h6v20c0 3 4 3 4 0V12l-4-4" fill="none" stroke="#999" stroke-width="2"/><path d="M2 43h28" stroke="#999" stroke-width="2"/></svg>
    <h4>Fuel Bill</h4>It is a long established fact that a<br>reader will be distracted...
  </div>
  <div class="abs bill" style="left:738px">
    <svg width="40" height="48"><rect x="8" y="2" width="24" height="44" rx="3" fill="none" stroke="#999" stroke-width="2"/><rect x="11" y="8" width="18" height="30" fill="#999"/><circle cx="20" cy="42" r="1.8" fill="#999"/></svg>
    <h4>Phone Bill</h4>It is a long established fact that a<br>reader will be distracted...
  </div>
  <svg class="abs strip-arrow" style="left:1031px" width="12" height="16"><path d="M3 2l6 6-6 6" fill="none" stroke="#999" stroke-width="1.5"/></svg>
</section>

<h2 class="abs welcome-title">WELCOME TO <b>TALLOW BROOK</b></h2>
<p class="abs welcome-tag">We charge only 36% and give over 12 months time to pay back, no fees, hidden costs etc.</p>
<p class="abs welcome-text">It is a long established fact that a reader will be distracted by the readable content of a page when looking at its layout. The point of using Lorem Ipsum is that it has a more-or-less normal distribution of letters, as opposed to using 'Content here, content here', making it look like readable English. Many desktop publishing packages and web page editors now use Lorem Ipsum as their default model text...</p>
<div class="abs divider"></div>

<article class="abs feature" style="left:171px">
  <h3>The Story</h3>
  <div class="photo" role="img" aria-label="Photo of a hand on a computer mouse beside a keyboard" style="background:linear-gradient(135deg,#eef2f5,#b9c6d1 60%,#6d7f8e)"></div>
  <p>It is a long established fact that a reader will be distracted by the readable content of a page when looking at its layout. The point of using Lorem Ipsum is that it has a more-or-less normal distribution...</p>
  <span class="btn">Read More</span>
</article>
<article class="abs feature" style="left:468px">
  <h3>Why tallowbrook.com</h3>
  <div class="photo" role="img" aria-label="Photo of a finger pressing a blue pay key on a keyboard" style="background:linear-gradient(135deg,#f3f3f3,#c7c9cc 55%,#5d88b5 70%,#d9dadc)"></div>
  <p>It is a long established fact that a reader will be distracted by the readable content of a page when looking at its layout. The point of using Lorem Ipsum is that it has a more-or-less normal distribution...</p>
  <span class="btn">Read More</span>
</article>
<article class="abs feature" style="left:766px">
  <h3>Are you eligible? Members</h3>
  <div class="photo" role="img" aria-label="Photo of a woman relaxing on a sofa with a laptop" style="background:linear-gradient(135deg,#8a7760,#d6c3a6 45%,#5c5a57 80%,#3e3d3c)"></div>
  <p>It is a long established fact that a reader will be distracted by the readable content of a page when looking at its layout. The point of using Lorem Ipsum is that it has a more-or-less normal distribution...</p>
  <span class="btn">Read More</span>
</article>

<section class="abs promo" role="img" aria-label="Dark photo of people working at laptops">
  <h2>Bills Paid Fast</h2>
  <p style="top:92px">It is a long established fact that a reader will be distracted by the readable content of a page when looking at its layout. The point of using Lorem Ipsum is that it has a more-or-less normal distribution of letters, as opposed to using 'Content here, content here', making it look like readable English. Many desktop publishing packages and web page editors now use Lorem Ipsum as their default model text, and a search for 'lorem ipsum' will uncover many web sites still in their infancy. Various versions have evolved over the years, sometimes by accident, sometimes on purpose.</p>
  <p style="top:205px">It is a long established fact that a reader will be distracted by the readable content of a page when looking at its layout. The point of using Lorem Ipsum is that it has a more-or-less normal distribution of letters, as opposed to using 'Content here, content here...</p>
  <div class="outline-btn">CLICK HERE&nbsp; FOR MORE INFO</div>
</section>

<h2 class="abs section-title" style="top:1750px;color:var(--green)">Our Clients</h2>
<p class="abs clients-text">It is a long established fact that a reader will be distracted by the readable content of a page when looking at its layout. The point of using Lorem Ipsum is that it has a more-or-less normal distribution of letters, as opposed to using 'Content here, content here...</p>
<div class="abs client" style="left:178px;top:1895px"><i></i>Nordvale</div>
<div class="abs client" style="left:393px;top:1895px"><i></i>Quillmere</div>
<div class="abs client" style="left:610px;top:1895px"><i></i>Pelvin</div>
<div class="abs client" style="left:826px;top:1895px"><i></i>Brightholm</div>
<div class="abs client" style="left:178px;top:2018px"><i></i>Solmerra</div>
<div class="abs client" style="left:393px;top:2018px"><i></i>Openfield Works</div>
<div class="abs client" style="left:610px;top:2018px"><i></i>Harlow Bay Hospital</div>
<div class="abs client" style="left:826px;top:2018px"><i></i>Cedarwick</div>

<section class="abs testimonials">
  <h2 class="section-title" style="position:absolute;top:34px;color:var(--white)">Testimonials</h2>
  <div class="t-arrow" style="left:174px"><svg width="28" height="28"><path d="M16 9l-5 5 5 5" fill="none" stroke="#fff" stroke-width="1.5"/></svg></div>
  <span class="qmark" style="left:246px;top:100px">“</span>
  <p class="quote">It is a long established fact that a reader will be distracted by the readable content of a page when looking at its layout. The point of using Lorem Ipsum is that it has a more-or-less normal distribution of letters, as opposed to using 'Content here, content here', making it look like readable English. Many desktop publishing packages and web page editors now...</p>
  <span class="qmark" style="left:930px;top:172px">”</span>
  <div class="t-arrow" style="left:998px"><svg width="28" height="28"><path d="M12 9l5 5-5 5" fill="none" stroke="#fff" stroke-width="1.5"/></svg></div>
  <p class="byline" style="top:239px">Posted by Marlon Keddy</p>
  <p class="byline" style="top:261px">27 march 2014</p>
</section>

<footer>
  <div class="abs site-footer"></div>
  <div class="abs footer-col" style="left:216px">Home<br>The Story<br>Why tallowbrook.com<br>Are you eligible? Members<br>Clients</div>
  <div class="abs footer-col" style="left:437px">Home<br>The Story<br>Why tallowbrook.com<br>Are you eligible? Members<br>Clients</div>
  <div class="abs footer-col" style="left:661px">Home<br>The Story<br>Why tallowbrook.com<br>Are you eligible? Members<br>Clients</div>
  <div class="abs social" style="top:2521px"><i></i>: Friendwall</div>
  <div class="abs social" style="top:2561px"><i></i>: Chirpline</div>
  <div class="abs social" style="top:2603px"><i></i>: Jobweave</div>
  <div class="abs footer-base">Copyright © 2014 Tallow-Brook. All Rights Reserved.</div>
</footer>

</body>
</html>
```